MRT Property - Business Cards

Looking for a business card & general letterhead, signage etc design for our new logo.

Colours:
000a20
0056a2
00b5ef
0088ce
68cef2

Fonts:
Poppins
Karla

Please keep look and feel of new brand - example in the zip package I sent.

```html
<!DOCTYPE html>
<html lang="en">
<head>
<meta charset="UTF-8">
<title>MRT Property – Business Cards</title>
<link href="https://fonts.googleapis.com/css2?family=Poppins:wght@400;500;700&family=Karla:wght@400;500&display=swap" rel="stylesheet">
<style>
  :root {
    --ink: #000a20;
    --navy: #12162d;
    --brand-blue: #0056a2;
    --card-blue: #0d57a8;
    --cyan: #00b5ef;
    --mid-blue: #0088ce;
    --sky: #68cef2;
    --white: #ffffff;
    --muted: #d7dbe6;
    --stage: #2a2a2e;
  }
  * { box-sizing: border-box; margin: 0; padding: 0; }
  html, body { width: 1200px; height: 900px; overflow: hidden; }
  body {
    background: var(--stage);
    font-family: "Karla", sans-serif;
    position: relative;
  }
  .card {
    position: absolute;
    width: 600px;
    height: 340px;
    border-radius: 22px;
    overflow: hidden;
  }
  .card--front {
    left: 110px;
    top: 70px;
    background: var(--card-blue);
    display: flex;
    align-items: center;
    justify-content: center;
  }
  .card--back {
    left: 490px;
    top: 470px;
    background: var(--navy);
  }
  .wordmark {
    display: flex;
    align-items: center;
    gap: 18px;
    font-family: "Poppins", sans-serif;
    font-weight: 700;
    color: var(--white);
    letter-spacing: 0.02em;
  }
  .wordmark__dot {
    border-radius: 50%;
    background: var(--sky);
    flex: none;
  }
  .card--front .wordmark { font-size: 54px; }
  .card--front .wordmark__dot { width: 46px; height: 46px; }

  .back__content {
    position: absolute;
    left: 44px;
    top: 38px;
    color: var(--white);
  }
  .card--back .wordmark { font-size: 34px; gap: 12px; }
  .card--back .wordmark__dot { width: 26px; height: 26px; }

  .person { margin-top: 26px; }
  .person__name {
    font-family: "Poppins", sans-serif;
    font-weight: 500;
    font-size: 22px;
    line-height: 1.1;
  }
  .person__title {
    font-size: 14px;
    color: var(--muted);
    margin-top: 2px;
  }
  .address {
    font-size: 14px;
    line-height: 1.35;
    margin-top: 14px;
    color: var(--muted);
    font-style: normal;
  }
  .contact {
    list-style: none;
    margin-top: 14px;
    font-size: 14px;
    color: var(--muted);
  }
  .contact li {
    display: flex;
    align-items: center;
    gap: 10px;
    line-height: 1.7;
  }
  .contact svg { width: 14px; height: 14px; flex: none; }
  .back__band {
    position: absolute;
    left: 0;
    right: 0;
    bottom: 0;
    height: 10px;
    background: var(--brand-blue);
  }
</style>
</head>
<body>
  <section class="card card--front" aria-label="Business card front">
    <div class="wordmark">
      <span class="wordmark__dot"></span>
      <span>MRT Property</span>
    </div>
  </section>

  <section class="card card--back" aria-label="Business card back">
    <div class="back__content">
      <div class="wordmark">
        <span class="wordmark__dot"></span>
        <span>MRT Property</span>
      </div>
      <div class="person">
        <p class="person__name">Daniel Brooks</p>
        <p class="person__title">Managing Director</p>
      </div>
      <address class="address">
        204 Cedar Ridge Lane<br>
        Brandon, MS 39047
      </address>
      <ul class="contact">
        <li>
          <svg viewBox="0 0 24 24" aria-hidden="true"><path fill="var(--mid-blue)" d="M6.6 10.8a15 15 0 0 0 6.6 6.6l2.2-2.2c.3-.3.7-.4 1-.2 1.1.4 2.3.6 3.6.6.6 0 1 .4 1 1V20c0 .6-.4 1-1 1A17 17 0 0 1 3 4c0-.6.4-1 1-1h3.5c.6 0 1 .4 1 1 0 1.3.2 2.5.6 3.6.1.3 0 .7-.2 1z"/></svg>
          <span>555.210.4477</span>
        </li>
        <li>
          <svg viewBox="0 0 24 24" aria-hidden="true"><rect x="2" y="5" width="20" height="14" rx="2" fill="var(--mid-blue)"/><path d="M3 6l9 7 9-7" fill="none" stroke="var(--navy)" stroke-width="2"/></svg>
          <span>info@mrtproperty.com</span>
        </li>
        <li>
          <svg viewBox="0 0 24 24" aria-hidden="true"><circle cx="12" cy="12" r="9" fill="none" stroke="var(--mid-blue)" stroke-width="2"/><path d="M3 12h18M12 3c3 3.5 3 14.5 0 18M12 3c-3 3.5-3 14.5 0 18" fill="none" stroke="var(--mid-blue)" stroke-width="1.6"/></svg>
          <span>www.mrtproperty.com</span>
        </li>
      </ul>
    </div>
    <div class="back__band"></div>
  </section>
</body>
</html>
```